Webdesign für Steuerberaterin
Zielgruppe
Ich bin Steuerberaterin. Meine Zielgruppe sind sowohl Privatpersonen als auch Unternehmer sowie Männer und Frauen.
Aufgabenstellung
Bitte mein Logo und Foto mit berücksichtigen. Ich möchte keine Website, auf der alle 'Reiter' als eine Seite von oben nach unten durchlaufen. Sondern wirklich einzelne, voneinander getrennte Seiten.

```html
<!DOCTYPE html>
<html lang="de">
<head>
<meta charset="utf-8">
<title>Maren Brodtke – Steuerberaterin</title>
<link rel="stylesheet" href="https://fonts.googleapis.com/css2?family=Crimson+Text&family=PT+Sans:wght@400;700&display=swap">
<style>
  :root {
    --sidebar: #1c1a1f;
    --gold: #b08a2e;
    --band: #dfb83c;
    --text: #4a4a4a;
    --page: #ffffff;
    --photo-light: #ecebea;
    --photo-mid: #d9d6d3;
  }
  * { margin: 0; padding: 0; box-sizing: border-box; }
  html, body { width: 1200px; height: 768px; overflow: hidden; background: var(--page); }
  body { position: relative; font-family: "PT Sans", sans-serif; color: var(--text); }

  .sidebar { position: absolute; left: 0; top: 0; width: 307px; height: 744px; background: var(--sidebar); }
  .main-nav { position: absolute; left: 80px; top: 184px; list-style: none; }
  .main-nav li { height: 44px; }
  .main-nav a { color: var(--gold); text-decoration: none; font-size: 14px; }

  .brand { position: absolute; left: 344px; top: 104px; width: 200px; text-align: center;
    font-family: "Crimson Text", serif; font-size: 24px; color: var(--gold); }

  .portrait { position: absolute; left: 194px; top: 186px; width: 401px; height: 292px;
    background: radial-gradient(ellipse at 50% 55%, var(--photo-light), var(--photo-mid)); }

  .welcome { position: absolute; left: 650px; top: 172px; width: 513px; text-align: center; }
  .welcome h1 { font-family: "Crimson Text", serif; font-weight: 400; font-size: 25px; color: var(--gold);
    padding-bottom: 12px; border-bottom: 2px solid var(--gold); }
  .welcome .lead { font-weight: 700; font-size: 15px; margin-top: 32px; }
  .welcome p { font-size: 14.5px; line-height: 19.5px; margin-top: 20px; }
  .welcome p.first { margin-top: 22px; }

  .footer-band { position: absolute; left: 0; bottom: 0; width: 1200px; height: 24px; background: var(--band); }
</style>
</head>
<body>
  <aside class="sidebar">
    <ul class="main-nav">
      <li><a href="#">Über mich</a></li>
      <li><a href="#">Leistungen</a></li>
      <li><a href="#">Kontakt</a></li>
      <li><a href="#">Impressum</a></li>
    </ul>
  </aside>

  <div class="brand">Maren Brodtke</div>

  <div class="portrait" role="img" aria-label="Porträtfoto der Steuerberaterin vor heller Steinwand"></div>

  <main class="welcome">
    <h1>Schön, dass Sie da sind</h1>
    <div class="lead">Ich freue mich, dass Sie den Weg zu mir gefunden haben!</div>
    <p class="first">Sie sind bei mir genau richtig:<br>
      Egal, ob Sie Privatperson sind, die Ihre Einkommensteuer-Erklärung<br>
      in vertrauensvolle Hände geben möchte,<br>
      oder Unternehmer, der sich z.B. das „Rundum-Sorglos-Paket“<br>
      mit Buchführung, Jahresabschluss und Steuererklärungen wünscht.</p>
    <p>Schauen Sie sich hier gerne um und melden Sie sich bei mir – ich bin bei jedem<br>
      steuerlichen Thema gerne Ihr kompetenter und zuverlässiger Ansprechpartner.</p>
    <p>Für mich ist es eine Selbstverständlichkeit,<br>
      dass ich auch nach mehr als 12 Jahren Berufserfahrung<br>
      durch permanente Fortbildungen immer auf dem aktuellsten Stand<br>
      der relevanten Gesetze und Verordnungen bin.<br>
      Nur so kann ich Sie bestmöglich beraten.</p>
  </main>

  <div class="footer-band"></div>
</body>
</html>
```